U.S. Popcorn company needs business cards

We are a popcorn company that manufactures popcorn and sells it to grocery stores worldwide. Our theme is "Americana" and our logo is U.S. route 66 which is the most famous highway in the U.S.

We would like the design to be simple and to use both sides. On the back side we would like to see just the logo and website. The front would be normal details

Target Market(s)

Wholesalers, grocers and distributors

Industry/Entity Type

Manufacture

Contact Information for Business Card

Business name: Prairie Lantern Popcorn
Phone: +1 555 308 4726
Email: Dale@prairielanternpopcorn.com
website: www.prairielanternpopcorn.com
Tag Line: "Crunch worth sharing"
Name: Dale Whitcombe
Title: Founder/President

Requirements
Must have
• Either this design should be fun or clean and simple. I will let you show me your thougths.
Nice to have
• Anything that ties in the real Hwy Route 66.
• Colors might need to be red, white and blue incorporated.
Should not have
• Not be too busy.

```html
<!DOCTYPE html>
<html lang="en">
<head>
<meta charset="utf-8">
<title>Prairie Lantern Popcorn – Business Cards</title>
<link href="https://fonts.googleapis.com/css2?family=Montserrat:wght@400;600;700&display=swap" rel="stylesheet">
<style>
  :root {
    --backdrop: #1c1c1d;
    --card: #161617;
    --card-edge: #2a2a2b;
    --silver: #9a9a9c;
    --white: #f2f2f2;
    --rule: #bdbdbd;
    --red: #d42a22;
    --blue: #16306e;
    --font: "Montserrat", sans-serif;
  }
  * { box-sizing: border-box; margin: 0; padding: 0; }
  html, body {
    width: 1200px; height: 793px; overflow: hidden;
    background: var(--backdrop);
    font-family: var(--font);
  }
  .stage { position: relative; width: 1200px; height: 793px; }
  .card {
    position: absolute; top: 246px;
    width: 520px; height: 300px;
    background: var(--card);
    border-radius: 12px;
    overflow: hidden;
    box-shadow: 0 0 0 1px var(--card-edge);
  }
  .card--back { left: 60px; }
  .card--front { left: 620px; }

  /* back */
  .back-wordmark {
    position: absolute; inset: 0;
    display: flex; align-items: center; justify-content: center;
    gap: 12px;
  }
  .back-wordmark__dot {
    width: 18px; height: 18px; border-radius: 50%;
    background: var(--silver);
  }
  .back-wordmark__name {
    color: var(--silver); font-weight: 700; font-size: 22px;
    letter-spacing: 0.5px;
  }

  /* front */
  .brand {
    position: absolute; left: 30px; top: 40px;
    display: flex; align-items: center; gap: 10px;
  }
  .brand__dot {
    width: 16px; height: 16px; border-radius: 50%; background: var(--white);
  }
  .brand__name {
    color: var(--white); font-weight: 700; font-size: 17px; line-height: 1.25;
    width: 150px;
  }
  .person { position: absolute; right: 30px; top: 92px; text-align: right; }
  .person__name { color: var(--red); font-weight: 600; font-size: 18px; }
  .person__title { color: var(--white); font-size: 12px; margin-top: 2px; }
  .divider {
    position: absolute; left: 30px; top: 142px;
    width: 380px; height: 1px; background: var(--rule);
  }
  .contacts { position: absolute; left: 30px; top: 162px; list-style: none; }
  .contacts li {
    display: flex; align-items: center; gap: 12px;
    color: var(--white); font-size: 13px; height: 21px;
  }
  .contacts svg { width: 12px; height: 12px; flex: none; }
  .contacts .accent { color: var(--red); }
  .bands { position: absolute; left: 0; bottom: 0; width: 520px; height: 60px; }
  .tagline {
    position: absolute; right: 28px; bottom: 20px;
    color: var(--white); font-size: 14px; white-space: nowrap;
  }
  .tagline strong { font-weight: 700; }
</style>
</head>
<body>
<main class="stage">

  <section class="card card--back" aria-label="Card back">
    <div class="back-wordmark">
      <span class="back-wordmark__dot"></span>
      <span class="back-wordmark__name">Prairie Lantern Popcorn</span>
    </div>
  </section>

  <section class="card card--front" aria-label="Card front">
    <div class="brand">
      <span class="brand__dot"></span>
      <span class="brand__name">Prairie Lantern Popcorn</span>
    </div>

    <div class="person">
      <p class="person__name">Dale Whitcombe</p>
      <p class="person__title">Founder/President</p>
    </div>

    <div class="divider"></div>

    <ul class="contacts">
      <li>
        <svg viewBox="0 0 12 12" fill="var(--red)"><path d="M2.5 1h2l1 3-1.5 1a6 6 0 0 0 3 3l1-1.5 3 1v2a1 1 0 0 1-1 1A10 10 0 0 1 1.5 2a1 1 0 0 1 1-1z"/></svg>
        +1 555 308 4726
      </li>
      <li>
        <svg viewBox="0 0 12 12" fill="var(--red)"><path d="M1 2.5h10v7H1z"/><path d="M1 2.5l5 4 5-4" stroke="var(--card)" stroke-width="1" fill="none"/></svg>
        Dale@prairielanternpopcorn.com
      </li>
      <li>
        <svg viewBox="0 0 12 12" fill="none" stroke="var(--red)" stroke-width="1.2"><circle cx="6" cy="6" r="4.8"/><ellipse cx="6" cy="6" rx="2" ry="4.8"/><path d="M1.2 6h9.6"/></svg>
        <span>www.<span class="accent">prairielanternpopcorn</span>.com</span>
      </li>
    </ul>

    <svg class="bands" viewBox="0 0 520 60" preserveAspectRatio="none" aria-hidden="true">
      <polygon points="0,34 285,34 274,60 0,60" fill="var(--red)"/>
      <polygon points="300,0 520,0 520,60 276,60" fill="var(--blue)"/>
    </svg>
    <p class="tagline">"<strong>Crunch</strong> worth sharing"</p>
  </section>

</main>
</body>
</html>
```